VORELT B2B portal design
Fantastic design work, top communication and fast design changes! Many thanks,Jarek & Lutz from VORELT
Zielgruppe
We are a B2B Cloud Services StartUp that creates B2B logistics & supply chain processes between customer and its suppliers.
Aufgabenstellung
We need a modern responsive able design, that should consider that we are NOT presenting goods or clothes or similar on the portal pages but we show mainly data grids, kpi dashboards, forms, and setting panels to our customer and their suppliers.
The design must be clean and straight not to distract people from the important information in these data grids, kpi dashboards, forms, and settings panels.
We need our logo perfectly embedded and the pages coloured around from grey to blue.
The Designer must be able to deliver a design and transfer it to a highly responsive HTML (5) template (without technical content or further functionality). This our programmers will implement afterwards in .Net.
We need in total 3 page templates:
1. Login Page
2. Main Page with overview over the following services text (each one shown in one tile)
"ZMS (Time Frame Management)"
"DMS (Document Management)"
"REMS (Reporting Management)"
-> Note: At the end we will have up to 12 or more tiles (services) so the design should be additive
3. Data grid (e.g. list of customers)/form (e.g. customer registration form) page to show some data grid with database data
See samples for each page enclosed!!

```html
<!DOCTYPE html>
<html lang="en">
<head>
<meta charset="utf-8">
<title>VORELT Portal – Dashboard</title>
<link rel="stylesheet" href="https://fonts.googleapis.com/css2?family=Open+Sans:wght@400;600;700&display=swap">
<style>
:root{
  --navy:#0d2a45;
  --chrome:#e2e7ea;
  --chrome-line:#c9d0d5;
  --page:#f5f7f9;
  --text:#1f2d3a;
  --muted:#5e6770;
  --green:#5cb85c;
  --green-text:#3e9a3e;
  --blue:#4bafd3;
  --blue-text:#2b8fb4;
  --orange:#f0ad4e;
  --orange-text:#d78a1c;
  --grid-line:#d3d8dc;
  --grid-head:#e3e7ea;
  --grid-foot:#f5f5f6;
  --white:#ffffff;
}
*{box-sizing:border-box;margin:0;padding:0}
html,body{width:1200px;height:948px;overflow:hidden}
body{font-family:"Open Sans",sans-serif;background:var(--page);color:var(--text);position:relative}

.topbar{position:absolute;left:0;top:0;width:1200px;height:138px;background:var(--chrome);border-bottom:1px solid var(--chrome-line)}
.brand{position:absolute;left:20px;top:44px;display:flex;align-items:center;gap:10px;font-size:40px;font-weight:700;color:var(--navy);letter-spacing:1px}
.brand-dot{width:16px;height:16px;border-radius:50%;background:var(--navy)}
.user{position:absolute;right:16px;top:36px;display:flex;align-items:center}
.user-text{text-align:right;margin-right:12px}
.user-name{font-size:19px;font-weight:600;color:var(--navy);line-height:24px}
.user-role{font-size:14px;color:var(--text);line-height:18px}
.avatar{width:66px;height:66px;border-radius:50%;background:linear-gradient(150deg,#8a8480,#3b3735);border:2px solid #bfc5c9}
.caret{margin-left:10px;width:0;height:0;border-left:5px solid transparent;border-right:5px solid transparent;border-top:6px solid #7a838a}

.sidebar{position:absolute;left:0;top:138px;width:265px;height:810px;background:var(--chrome)}
.nav-item{height:61px;display:flex;align-items:center;padding-left:18px;font-size:19px;color:var(--navy);border-bottom:1px solid var(--chrome-line)}
.nav-item svg{width:28px;height:24px;margin-right:10px;fill:none;stroke:currentColor;stroke-width:2}
.nav-item.active{background:var(--navy);color:var(--white);border-bottom-color:var(--navy)}
.nav-item.logout{border-bottom:none}

.tiles{position:absolute;left:302px;top:218px;display:flex;gap:35px}
.tile{width:265px;height:221px;background:var(--white);border:1px solid #d6dade;border-radius:3px;box-shadow:0 1px 3px rgba(0,0,0,.08);overflow:hidden;text-align:center}
.tile-art{height:157px;display:flex;align-items:center;justify-content:center}
.tile-art svg{width:116px;height:116px;fill:none;stroke:var(--white);stroke-width:5;stroke-linecap:round;stroke-linejoin:round}
.tile-title{font-size:21px;font-weight:600;margin-top:6px;line-height:26px}
.tile-sub{font-size:15px;line-height:20px}
.tile.zms .tile-art{background:var(--green)} .tile.zms .tile-title,.tile.zms .tile-sub{color:var(--green-text)}
.tile.dms .tile-art{background:var(--blue)} .tile.dms .tile-title,.tile.dms .tile-sub{color:var(--blue-text)}
.tile.rems .tile-art{background:var(--orange)} .tile.rems .tile-title,.tile.rems .tile-sub{color:var(--orange-text)}

.section-title{position:absolute;left:302px;top:510px;font-size:22px;color:var(--text)}
.grid{position:absolute;left:302px;top:552px;width:872px;border:1px solid var(--grid-line);background:var(--white)}
.grid table{width:100%;border-collapse:collapse}
.grid th,.grid td{border-right:1px solid var(--grid-line);border-bottom:1px solid var(--grid-line);text-align:left;padding-left:13px}
.grid th:last-child,.grid td:last-child{border-right:none}
.grid th{background:var(--grid-head);height:39px;font-size:16px;font-weight:400;color:var(--text)}
.grid td{height:40px;font-size:13px;color:var(--muted)}
.grid .check{width:73px;padding-left:20px}
.box{display:block;width:14px;height:14px;border:1px solid #8e969c;border-radius:2px;background:linear-gradient(#fff,#e8eaec)}
.grid-foot{height:59px;background:var(--grid-foot);display:flex;align-items:center;justify-content:flex-end;padding-right:9px}
.pager{display:flex;height:36px;align-items:center;background:var(--white)}
.pager .end{background:var(--navy);color:var(--white);font-size:13px;font-weight:700;height:36px;padding:0 14px;display:flex;align-items:center;border-radius:3px}
.pager .pages{display:flex;align-items:center;padding:0 14px 0 29px;font-size:14px;color:var(--text);gap:0}
.pager .pages span{padding:0 5px;height:36px;line-height:36px}
.pager .pages .current{background:#b3b7ba;color:var(--white);padding:0 9px}
</style>
</head>
<body>
<header class="topbar">
  <div class="brand"><span class="brand-dot"></span>VORELT</div>
  <div class="user">
    <div class="user-text">
      <div class="user-name">Mark Doyle</div>
      <div class="user-role">Gest User</div>
    </div>
    <div class="avatar" role="img" aria-label="User profile photo"></div>
    <div class="caret"></div>
  </div>
</header>

<nav class="sidebar">
  <div class="nav-item active"><svg viewBox="0 0 28 24"><path d="M3 19a11 11 0 1 1 22 0z"/><path d="M14 18l5-7"/></svg>Dashboard</div>
  <div class="nav-item"><svg viewBox="0 0 28 24"><circle cx="14" cy="12" r="10.5"/><circle cx="14" cy="9" r="3.5" fill="currentColor"/><path d="M7 19c2-4 12-4 14 0" fill="currentColor"/></svg>Profile</div>
  <div class="nav-item"><svg viewBox="0 0 28 24"><circle cx="9" cy="10" r="5" fill="currentColor"/><circle cx="20" cy="17" r="3.5" fill="currentColor"/><circle cx="21" cy="5" r="2.5" fill="currentColor"/></svg>Settings</div>
  <div class="nav-item"><svg viewBox="0 0 28 24"><path d="M4 21V12M9 21V8M14 21V11M19 21V6M24 21V10M2 21h24M4 10l5-4 5 3 5-5 5 4"/></svg>Charts</div>
  <div class="nav-item"><svg viewBox="0 0 28 24"><rect x="3" y="3" width="22" height="18"/><path d="M3 9h22M3 15h22M9 3v18"/></svg>Forms</div>
  <div class="nav-item"><svg viewBox="0 0 28 24"><circle cx="14" cy="12" r="9.5"/><path d="M10 10l4 4 4-4"/></svg>Dropdown</div>
  <div class="nav-item logout"><svg viewBox="0 0 28 24"><path d="M15 5H6v15h15v-9M12 14L23 3M17 3h6v6"/></svg>Logout</div>
</nav>

<main>
  <section class="tiles">
    <div class="tile zms">
      <div class="tile-art"><svg viewBox="0 0 116 116"><path d="M96 44A40 40 0 1 1 58 18"/><path d="M32 100l8-6-2-9"/><path d="M70 18a40 40 0 0 1 20 12" stroke-dasharray="6 8"/><text x="58" y="68" font-family="Open Sans,sans-serif" font-size="28" fill="#fff" stroke="none" text-anchor="middle">24</text></svg></div>
      <div class="tile-title">ZMS</div>
      <div class="tile-sub">Time Frame Management System</div>
    </div>
    <div class="tile dms">
      <div class="tile-art"><svg viewBox="0 0 116 116"><path d="M14 54l10-18h68l10 18v46H14z"/><path d="M14 54h88"/><path d="M34 50V24h48v26M40 18h36"/><circle cx="58" cy="78" r="6"/></svg></div>
      <div class="tile-title">DMS</div>
      <div class="tile-sub">Document Management System</div>
    </div>
    <div class="tile rems">
      <div class="tile-art"><svg viewBox="0 0 116 116"><rect x="28" y="12" width="60" height="86"/><path d="M94 22v84H40M40 30h36M40 42h36M40 54h20M38 80l10-12 12 12 16-14"/></svg></div>
      <div class="tile-title">REMS</div>
      <div class="tile-sub">Reporting Management System</div>
    </div>
  </section>

  <h2 class="section-title" style="font-weight:400">Grid Styling</h2>
  <section class="grid">
    <table>
      <thead>
        <tr><th class="check"><span class="box"></span></th><th style="width:143px">Record</th><th style="width:120px">Batch ID</th><th style="width:205px">Keyword</th><th style="width:108px">Status</th><th>Reason</th></tr>
      </thead>
      <tbody>
        <tr><td class="check"><span class="box"></span></td><td>Danish</td><td>Yes</td><td>Some Dummy Text</td><td>Rejected</td><td>Policy Error: (adult)</td></tr>
        <tr><td class="check"><span class="box"></span></td><td>Danish</td><td>Yes</td><td>Some Dummy Text</td><td>Rejected</td><td>Policy Error: (adult)</td></tr>
        <tr><td class="check"><span class="box"></span></td><td>Danish</td><td>Yes</td><td>Some Dummy Text</td><td>Rejected</td><td>Policy Error: (adult)</td></tr>
        <tr><td class="check"><span class="box"></span></td><td>Danish</td><td>Yes</td><td>Some Dummy Text</td><td>Rejected</td><td>Policy Error: (adult)</td></tr>
      </tbody>
    </table>
    <div class="grid-foot">
      <div class="pager">
        <span class="end">FIRST</span>
        <div class="pages"><span class="current">1</span><span>2</span><span>3</span><span>4</span><span>5</span><span>6</span><span>7</span><span>8</span><span>9</span><span>10</span><span>....</span><span>100</span></div>
        <span class="end">LAST</span>
      </div>
    </div>
  </section>
</main>
</body>
</html>
```